Creative, fresh business card design for Ripplecraft Facades

We need a fresh, creative business card design for Ripplecraft Facades. We are the manufacturer of Ripplecraft Facades in Australia. Wall panels are 2400 x 1200mm panels made from MDF and feature 3D patterns on the face of the panel. The colours to be used are green, silver/grey and white RGB
Red 187
Green 207
Blue 65.

An idea is to possibly use a watermark of one of our designs as a background (like on the "Grids" design on the left hand side of page 2 of our brochure).

Target Market(s)

Interior designers, architects, builders and home renovators

Industry/Entity Type

Business

Contact Information for Business Card

Details to go on the card are:
Our logo (attached),
Slogan: "Decorative panels for interiors and exteriors",
Contact name,
Position,
Mobile phone number,
Business address,
Business phone,
Business fax,
Website and
Email address.

I have attached a few images of our panels and our brochure for reference.

The colours of the business card should feature our logo colours which are: RGB
Red 187
Green 207
Blue 65

Requirements
Must have
• Very modern fonts and design. Some of the designs shown especially the "Prisms" design which is a popular design.
Nice to have
• Creative but simple design. Very contemporary.
Should not have
• Anything ornate or old fashioned.

```html
<!DOCTYPE html>
<html lang="en">
<head>
<meta charset="utf-8">
<title>Ripplecraft Facades – Business Card</title>
<link rel="stylesheet" href="https://fonts.googleapis.com/css2?family=Open+Sans:wght@400&family=Crimson+Text&display=swap">
<style>
  :root {
    --backdrop: #2e2c2e;
    --card-white: #f4f2ef;
    --panel-light: #faf9f7;
    --panel-shade: #dedbd6;
    --brand-green: #bbcf41;
    --deep-green: #246400;
    --silver: #8a8a8a;
    --ink-dark: #3a3a3a;
    --text-light: #ffffff;
  }
  html, body {
    margin: 0;
    padding: 0;
    width: 1200px;
    height: 1000px;
    overflow: hidden;
    background: var(--backdrop);
  }
  .card {
    position: absolute;
    left: 100px;
    top: 220px;
    width: 1000px;
    height: 559px;
    background: var(--card-white);
    box-shadow: 0 14px 30px rgba(0, 0, 0, 0.55);
    overflow: hidden;
  }
  .panel-texture {
    position: absolute;
    inset: 0;
    background: linear-gradient(170deg, var(--panel-light) 0%, var(--panel-shade) 45%, var(--panel-light) 70%, var(--panel-shade) 100%);
  }
  .wave-band {
    position: absolute;
    inset: 0;
    width: 1000px;
    height: 559px;
  }
  .wave-band path { fill: var(--deep-green); }
  .brand {
    position: absolute;
    left: 0;
    right: 0;
    top: 40px;
    display: flex;
    flex-direction: column;
    align-items: center;
  }
  .brand-name {
    display: flex;
    align-items: center;
    gap: 14px;
    font-family: "Open Sans", sans-serif;
    font-size: 36px;
    color: var(--deep-green);
    letter-spacing: 0.5px;
  }
  .brand-square {
    width: 34px;
    height: 34px;
    background: var(--brand-green);
  }
  .slogan {
    margin: 18px 0 0 0;
    font-family: "Crimson Text", serif;
    font-size: 22px;
    line-height: 24px;
    color: var(--ink-dark);
    letter-spacing: 1px;
    text-align: left;
  }
  .contact {
    position: absolute;
    left: 29px;
    top: 378px;
    margin: 0;
    padding: 0;
    list-style: none;
    font-family: "Open Sans", sans-serif;
    font-size: 21px;
    line-height: 32px;
    color: var(--text-light);
  }
</style>
</head>
<body>
  <article class="card">
    <div class="panel-texture" role="img" aria-label="Photograph of a white wall panel with a flowing rippled 3D relief pattern"></div>
    <svg class="wave-band" viewBox="0 0 1000 559" aria-hidden="true">
      <path d="M0,340 C60,305 110,288 165,288 C270,288 380,372 520,392 C640,410 740,330 850,312 C910,302 960,297 1000,295 L1000,559 L0,559 Z"/>
    </svg>
    <header class="brand">
      <div class="brand-name"><span class="brand-square"></span>Ripplecraft Facades</div>
      <p class="slogan">decorative panels for<br>interiors &amp; landscapes</p>
    </header>
    <ul class="contact">
      <li>Telephone: 02 9000 4182</li>
      <li>Business fax: 02 9000 4196</li>
      <li>14 Kessel Lane, Marrowvale NSW 2190</li>
      <li>www.ripplecraftfacades.com.au</li>
      <li>sales@ripplecraftfacades.com.au</li>
    </ul>
  </article>
</body>
</html>
```